Indy Film Production Company/Studio

We need a business card designed from an existing logo. We are a digital studio/production company that caters to creating genre entertainment, like Action, Horror, and martial arts. The card along with the logo will be used to Brand the company from letter heads to banners. The design will also be used for postcards and Brochures. It should be professional and masculine.
Updates

Thank you to all the designers who have participated. I'm narrowing down who it will be. Thank you again.

Target Market(s)

Investors, Networks, Producers, and actors

Industry/Entity Type

Film Production

Contact Information for Business Card

Teodoro Valbuena
Producer/Writer/Director
www.kestrelpicturehouse.example

Requirements
Must have
• Website address, Facebook icon and Twitter icon possibly in the back of the card.
Nice to have
• Logline of Company: Follow The Action.

```html
<!DOCTYPE html>
<html lang="en">
<head>
<meta charset="utf-8">
<title>Kestrel Picture House – Business Card</title>
<link rel="stylesheet" href="https://fonts.googleapis.com/css2?family=Montserrat:wght@400;500;800&display=swap">
<style>
  :root {
    --stage: #2b2b2b;
    --card-black: #000000;
    --accent-red: #e8202c;
    --white: #ffffff;
    --silver: #d9d9d9;
  }
  * { margin: 0; padding: 0; box-sizing: border-box; }
  html, body { width: 1200px; height: 900px; overflow: hidden; }
  body {
    background: var(--stage);
    font-family: "Montserrat", Arial, sans-serif;
    position: relative;
  }
  .card {
    position: absolute;
    left: 250px;
    width: 700px;
    height: 400px;
    overflow: hidden;
    box-shadow: 0 10px 30px rgba(0,0,0,.55);
  }
  .card--front { top: 30px; }
  .card--back  { top: 470px; }
  .card__shape { position: absolute; inset: 0; width: 100%; height: 100%; }

  .brand-name {
    position: absolute;
    color: var(--silver);
    font-weight: 800;
    text-transform: uppercase;
    line-height: 1.05;
    letter-spacing: 1px;
  }
  .card--front .brand-name {
    left: 180px; top: 120px;
    font-size: 44px;
  }
  .card--back .brand-name {
    left: 190px; top: 270px;
    font-size: 34px;
  }

  .front-web {
    position: absolute;
    right: 36px; bottom: 40px;
    color: var(--white);
    font-size: 17px;
    font-weight: 400;
    letter-spacing: .5px;
  }
  .front-web .highlight { color: var(--accent-red); }

  .contact {
    position: absolute;
    right: 40px; top: 36px;
    text-align: right;
    color: var(--white);
  }
  .contact__name {
    color: var(--accent-red);
    font-size: 20px;
    font-weight: 500;
    letter-spacing: 1px;
    text-transform: uppercase;
  }
  .contact__role {
    font-size: 12px;
    letter-spacing: 1px;
    text-transform: uppercase;
    margin-bottom: 16px;
  }
  .contact__line {
    font-size: 14px;
    line-height: 22px;
    display: flex;
    justify-content: flex-end;
    align-items: center;
    gap: 8px;
  }
  .contact__icon { width: 12px; height: 12px; flex: none; }
  .social-dot {
    width: 12px; height: 12px; flex: none;
    border-radius: 50%;
    background: var(--accent-red);
  }
</style>
</head>
<body>

  <section class="card card--front">
    <svg class="card__shape" viewBox="0 0 700 400" preserveAspectRatio="none" aria-hidden="true">
      <rect width="700" height="400" fill="var(--accent-red)"/>
      <path d="M240 0 Q600 0 700 150 L700 400 L0 400 L0 0 Z" fill="var(--white)"/>
      <path d="M290 0 Q630 20 700 195 L700 400 L0 400 L0 0 Z" fill="var(--card-black)"/>
    </svg>
    <div class="brand-name">Kestrel<br>Picture House</div>
    <div class="front-web">www.<span class="highlight">kestrelpicturehouse</span>.example</div>
  </section>

  <section class="card card--back">
    <svg class="card__shape" viewBox="0 0 700 400" preserveAspectRatio="none" aria-hidden="true">
      <rect width="700" height="400" fill="var(--accent-red)"/>
      <path d="M0 0 L700 0 L700 40 Q700 300 440 400 L0 400 Z" fill="var(--white)"/>
      <path d="M0 0 L700 0 L700 0 Q675 290 400 400 L0 400 Z" fill="var(--card-black)"/>
    </svg>
    <div class="contact">
      <div class="contact__name">Teodoro Valbuena</div>
      <div class="contact__role">Producer / Writer / Director</div>
      <div class="contact__line">+330 2460-0173
        <svg class="contact__icon" viewBox="0 0 12 12"><path d="M2 1 L4.5 1 L5.5 3.5 L4 4.5 Q5 7 7.5 8 L8.5 6.5 L11 7.5 L11 10 Q6 11 1.5 5.5 Q1 3 2 1 Z" fill="var(--accent-red)"/></svg>
      </div>
      <div class="contact__line">info@kestrelpicturehouse.example
        <svg class="contact__icon" viewBox="0 0 12 12"><rect x="1" y="2.5" width="10" height="7" fill="none" stroke="var(--accent-red)" stroke-width="1.4"/><path d="M1 2.5 L6 6.5 L11 2.5" fill="none" stroke="var(--accent-red)" stroke-width="1.4"/></svg>
      </div>
      <div class="contact__line">www.kestrelpicturehouse.example
        <svg class="contact__icon" viewBox="0 0 12 12"><circle cx="6" cy="6" r="5" fill="none" stroke="var(--accent-red)" stroke-width="1.3"/><ellipse cx="6" cy="6" rx="2.2" ry="5" fill="none" stroke="var(--accent-red)" stroke-width="1"/><path d="M1 6 H11" stroke="var(--accent-red)" stroke-width="1"/></svg>
      </div>
      <div class="contact__line">/kestrelpicturehouse
        <span class="social-dot" role="img" aria-label="Social profile icon"></span>
      </div>
      <div class="contact__line">@kestrelpictures
        <span class="social-dot" role="img" aria-label="Social handle icon"></span>
      </div>
    </div>
    <div class="brand-name">Kestrel<br>Picture House</div>
  </section>

</body>
</html>
```